Italian restaurant needs new site

Need to make our website better.

Must have reservation module

Must be able to sell wine tasting tours and wine pairing tours and intégrate with dunmo desk

Blog

Social media

Wandervane ranking and last review.
Updates

Number of Pages Required

1 page

Font styles to use
Serif

Requirements
Must have
• Reservation module
• Marketplace to buy wine pairings and gift certificates
• Wandervane review
• Kindlepost posts
• All info from old site

```html
<!DOCTYPE html>
<html lang="en">
<head>
<meta charset="utf-8">
<title>Lumira Bistro – Site Design</title>
<link href="https://fonts.googleapis.com/css2?family=Noto+Serif:wght@400;700&family=Source+Sans+3:wght@600&family=Yellowtail&display=swap" rel="stylesheet">
<style>
:root{
  --board:#efefef;
  --wine:#7b1c23;
  --wine-bright:#8e1e26;
  --ink:#2a2a2a;
  --white:#ffffff;
  --soft:#d9d9d9;
  --field:rgba(0,0,0,.55);
  --field-line:rgba(255,255,255,.12);
}
*{margin:0;padding:0;box-sizing:border-box}
html,body{width:926px;height:1200px;overflow:hidden;background:var(--board)}
body{position:relative;font-family:"Noto Serif",serif;color:var(--white)}
.page-label{position:absolute;left:0;width:926px;text-align:center;font-size:8px;letter-spacing:2.6px;color:var(--ink)}
.screen{position:absolute;left:51px;width:823px;height:514px;overflow:hidden}
.sidebar{position:absolute;left:0;top:0;width:199px;height:100%;background:var(--wine)}
.brand{position:absolute;left:0;top:20px;width:199px;text-align:center}
.brand-mark{display:block;width:12px;height:12px;border-radius:50%;background:var(--white);margin:0 auto 8px}
.brand-name{font-size:22px;letter-spacing:2px;line-height:1}
.brand-sub{font-size:12px;letter-spacing:1.5px;margin-top:4px}
.brand-tag{font-size:7px;letter-spacing:.6px;margin:6px auto 0;width:130px;border-top:1px solid rgba(255,255,255,.45);padding-top:4px}
.nav{position:absolute;left:0;width:199px;text-align:center;font-size:8px;letter-spacing:2.4px}
.nav.active{font-size:13px;font-weight:700;letter-spacing:3.2px}
.social{position:absolute;left:0;top:458px;width:199px;display:flex;justify-content:center;gap:10px;font-size:7px}
.copy{position:absolute;left:0;top:486px;width:199px;text-align:center;font-size:6px}
.photo{position:absolute;left:199px;top:0;width:624px;height:100%;
  background:radial-gradient(ellipse at 45% 45%,#5a5a5a 0%,#3b3b3b 45%,#1f1f1f 100%)}
.topbar{position:absolute;left:217px;top:17px;display:flex;gap:14px;font-size:8px;letter-spacing:.8px;align-items:center}
.topbar span{display:flex;align-items:center;gap:5px}
.cart{position:absolute;left:783px;top:13px}
.dots{position:absolute;left:804px;display:flex;flex-direction:column;gap:6px;align-items:center}
.dots i{display:block;width:6px;height:6px;border-radius:50%;background:#8a8a8a}
.dots i.on{width:9px;height:9px;background:none;border:2px solid var(--wine-bright)}
.dot-label{position:absolute;font-size:8px;letter-spacing:1px;text-align:right;width:100px}
.content{position:absolute;left:199px;width:624px;text-align:center}
.hero-title{font-size:52px;font-weight:700;letter-spacing:1px;line-height:1}
.script{font-family:"Yellowtail",cursive;display:flex;align-items:center;justify-content:center;gap:10px}
.script::before,.script::after{content:"";width:44px;height:1px;background:rgba(255,255,255,.6)}
.lead{font-size:8px;line-height:14px;color:var(--soft)}
.btn{position:absolute;height:30px;border-radius:15px;font-family:"Source Sans 3",sans-serif;font-weight:600;font-size:10px;display:flex;align-items:center;justify-content:center}
.btn.ghost{border:1.5px solid var(--white)}
.btn.solid{background:var(--wine-bright)}
.field{position:absolute;height:29px;background:var(--field);border:1px solid var(--field-line);font-size:8px;color:#bdbdbd;padding:9px 8px}
</style>
</head>
<body>

<div class="page-label" style="top:25px">HOME PAGE</div>

<section class="screen" style="top:57px">
  <aside class="sidebar">
    <div class="brand">
      <span class="brand-mark"></span>
      <div class="brand-name">LUMIRA</div>
      <div class="brand-sub">BISTRO</div>
      <div class="brand-tag">ITALIAN CUISINE &amp; WINE BAR</div>
    </div>
    <div class="nav active" style="top:186px">HOME</div>
    <div class="nav" style="top:219px">MENU</div>
    <div class="nav" style="top:250px">RESERVATIONS</div>
    <div class="nav" style="top:281px">BLOG</div>
    <div class="nav" style="top:312px">REVIEWS</div>
    <div class="nav" style="top:342px">CONTACT</div>
    <div class="social"><span>Reelhall</span><span>Orbitly</span><span>Snapfold</span><span>Kindlepost</span></div>
    <div class="copy">© 2017 LUMIRA BISTRO. ALL RIGHTS RESERVED</div>
  </aside>
  <div class="photo" role="img" aria-label="Photo of friends toasting with wine glasses at a dinner table"></div>
  <div class="topbar">
    <span><svg width="7" height="9" viewBox="0 0 7 9"><rect x="0.5" y="0.5" width="6" height="8" rx="1" fill="none" stroke="#fff"/><rect x="2" y="6" width="3" height="1" fill="#fff"/></svg>+52 624 555 0190</span>
    <span><svg width="8" height="8" viewBox="0 0 8 8"><circle cx="4" cy="4" r="3.3" fill="none" stroke="#fff"/><path d="M4 2v2h1.6" stroke="#fff" fill="none"/></svg>OPEN DAILY FROM : 5 TO 12 AM</span>
  </div>
  <svg class="cart" width="26" height="16" viewBox="0 0 26 16"><path d="M3 7h9l-1.5 5h-6z" fill="#fff"/><circle cx="19" cy="5" r="5" fill="var(--wine-bright)"/><text x="19" y="7.5" font-size="7" fill="#fff" text-anchor="middle" font-family="Noto Serif, serif">0</text></svg>
  <div class="dot-label" style="left:662px;top:221px">HOME</div>
  <div class="dots" style="top:222px"><i class="on"></i><i></i><i></i><i></i><i></i></div>

  <div class="content" style="top:288px"><div class="hero-title">Lumira Bistro</div></div>
  <div class="content script" style="top:346px;font-size:18px">Italian Restaurant in Cabo San Lucas</div>
  <p class="content lead" style="top:376px;padding:0 120px">Lumira Bistro Located in the heart of downtown, across from Marisol Square, just two short blocks up from Harborlight Resort and the Cabo marina is Lumira Bistro, a place with great original Southern Italian and Mediterranean cuisine and a European touch.</p>
  <div class="btn ghost" style="left:398px;top:439px;width:109px">EXPLORE MORE</div>
  <div class="btn solid" style="left:514px;top:439px;width:109px">RESERVATIONS</div>
</section>

<div class="page-label" style="top:596px">RESERVATIONS PAGE</div>

<section class="screen" style="top:629px">
  <aside class="sidebar">
    <div class="brand">
      <span class="brand-mark"></span>
      <div class="brand-name">LUMIRA</div>
      <div class="brand-sub">BISTRO</div>
      <div class="brand-tag">ITALIAN CUISINE &amp; WINE BAR</div>
    </div>
    <div class="nav" style="top:189px">HOME</div>
    <div class="nav" style="top:219px">MENU</div>
    <div class="nav active" style="top:246px">RESERVATIONS</div>
    <div class="nav" style="top:281px">BLOG</div>
    <div class="nav" style="top:312px">REVIEWS</div>
    <div class="nav" style="top:342px">CONTACT</div>
    <div class="social"><span>Reelhall</span><span>Orbitly</span><span>Snapfold</span><span>Kindlepost</span></div>
    <div class="copy">© 2017 LUMIRA BISTRO. ALL RIGHTS RESERVED</div>
  </aside>
  <div class="photo" role="img" aria-label="Dimmed photo of friends toasting with wine glasses at a dinner table"></div>
  <div class="topbar">
    <span><svg width="7" height="9" viewBox="0 0 7 9"><rect x="0.5" y="0.5" width="6" height="8" rx="1" fill="none" stroke="#fff"/><rect x="2" y="6" width="3" height="1" fill="#fff"/></svg>+52 624 555 0190</span>
    <span><svg width="8" height="8" viewBox="0 0 8 8"><circle cx="4" cy="4" r="3.3" fill="none" stroke="#fff"/><path d="M4 2v2h1.6" stroke="#fff" fill="none"/></svg>OPEN DAILY FROM : 5 TO 12 AM</span>
  </div>
  <svg class="cart" width="26" height="16" viewBox="0 0 26 16"><path d="M3 7h9l-1.5 5h-6z" fill="#fff"/><circle cx="19" cy="5" r="5" fill="var(--wine-bright)"/><text x="19" y="7.5" font-size="7" fill="#fff" text-anchor="middle" font-family="Noto Serif, serif">0</text></svg>
  <div class="dot-label" style="left:682px;top:245px">RESERVATIONS</div>
  <div class="dots" style="top:221px"><i></i><i></i><i></i><i class="on"></i><i></i><i></i></div>

  <div class="content script" style="top:92px;font-size:30px">Reservations</div>
  <div class="content script" style="top:128px;font-size:17px">Reservations for Lumira bistro Cabo San Lucas</div>
  <p class="content lead" style="top:161px;padding:0 55px">Reservations for Lumira bistro Cabo San Lucas open 7 days. For reservations less than 48 hours in advance, please call us at our local Mexico number: 624 555 0190. To make a reservation more than 48 hours in advance, please complete the following form. All official reservations will receive a 10-digit confirmation code. We have a 15 minute tolerance for all reservations. Thank you. We look forward to seeing you soon.</p>

  <div class="field" style="left:281px;top:229px;width:149px">Date</div>
  <div class="field" style="left:436px;top:229px;width:149px">Time</div>
  <div class="field" style="left:591px;top:229px;width:149px">Party Size</div>
  <div class="field" style="left:281px;top:264px;width:149px">Name</div>
  <div class="field" style="left:436px;top:264px;width:149px">Email</div>
  <div class="field" style="left:591px;top:264px;width:149px">Phone Number (Optional)</div>
  <div class="field" style="left:281px;top:300px;width:149px">Hotel Name</div>
  <div class="field" style="left:436px;top:300px;width:149px">Room Number</div>
  <div class="field" style="left:591px;top:300px;width:149px">Guest Email</div>
  <div class="field" style="left:281px;top:335px;width:459px;height:75px">Comments (Optional)</div>
  <div class="btn solid" style="left:456px;top:429px;width:109px">SEND</div>
</section>

</body>
</html>
```